Accountability Project Graphics

I want to create 10 social media graphics (new Instagram size 4:5 (1080 x 1350 pixels) focusing on our Quilvo Accountability App, using any of the 3 pictures attached. Use the attached pics only, NO RANDOM STOCK PHOTOGRAPHY. For the color scheme, use the landing page colors/fonts (attached).
You can add any of the 3 photos attached but I mainly need BOLD text that includes these headlines and sub-headlines on them.
Please NOTE for all the headlines below, also add this sub-headline on each graphic:
Stay Consistent with RT in Your Pocket!
Here are the headlines:
• Stop Starting Over Every Monday
• You don't need more willpower. You need more support
• Built for women who are tired of doing this alone
• When Motivation Fades, RT Checks In
• The Support System You've Been Missing
• Support When Motivation Disappears
• What if RT Checked in Every Day?
• The Missing Piece Isn't Another Diet
• Eat the food you love. Stay accountable every day.
• One Bad Meal Doesn't Mean You Failed
women over 40 trying to lose weight

```html
<!DOCTYPE html>
<html lang="en">
<head>
<meta charset="utf-8">
<title>Quilvo Accountability – Social Graphics</title>
<link href="https://fonts.googleapis.com/css2?family=Tinos:ital,wght@1,700&display=swap" rel="stylesheet">
<style>
  :root {
    --canvas: #f6f6f6;
    --plum: #5b2352;
    --night: #2e1c40;
    --rose: #c9587a;
    --blush: #e9a7bf;
    --white: #ffffff;
  }
  * { margin: 0; padding: 0; box-sizing: border-box; }
  html, body { width: 1200px; height: 1119px; overflow: hidden; background: var(--canvas); }
  body { position: relative; font-family: "Tinos", "Times New Roman", serif; font-style: italic; font-weight: 700; color: var(--white); }

  .post { position: absolute; width: 256px; height: 319px; overflow: hidden; }
  .photo { position: absolute; inset: 0; }
  .headline { position: absolute; letter-spacing: 0.5px; }
  .tagline { position: absolute; font-size: 11px; line-height: 1.3; }
  .divider { position: absolute; left: 50%; width: 145px; height: 1px; margin-left: -72px; background: var(--white); }
  .center { left: 0; right: 0; text-align: center; }

  .photo-solo-warm { background: linear-gradient(100deg, #8a3a6e 0%, #6e3a5e 45%, #2b2430 70%, #5c3a4a 100%); }
  .photo-hug { background: linear-gradient(170deg, #e7b6c9 0%, #c97c9c 35%, #4b3858 55%, #c55d86 80%, #7c3a6c 100%); }
  .photo-solo-pink { background: linear-gradient(100deg, #c5608a 0%, #a4507a 45%, #3c2a3d 70%, #b45878 100%); }
  .photo-solo-dark { background: linear-gradient(100deg, #3a3a3f 0%, #444046 40%, #1f2433 65%, #4a2430 100%); }
  .photo-solo-night { background: linear-gradient(180deg, #6a6a70 0%, #4f4a58 40%, #2e1c40 62%, #2e1c40 100%); }
  .photo-solo-rose { background: linear-gradient(100deg, #c4688c 0%, #b0577c 45%, #262a3a 65%, #c4688c 100%); }
  .photo-pair { background: linear-gradient(90deg, #33405e 0%, #d8d2d6 30%, #4b5c80 60%, #3c4a6a 100%); }
</style>
</head>
<body>

<section class="post" style="left:29px;top:51px;">
  <div class="photo photo-solo-warm" role="img" aria-label="Photo of RT smiling, standing by a pool table, with a plum tint"></div>
  <h2 class="headline" style="left:10px;top:63px;font-size:25px;line-height:26.5px;">Built for<br>women who<br>are tired of<br>doing this<br>alone</h2>
  <p class="tagline" style="left:9px;top:286px;font-size:9.5px;line-height:15px;">Stay Consistent<br>with RT in Your Pocket!</p>
</section>

<section class="post" style="left:313px;top:51px;">
  <div class="photo photo-hug" role="img" aria-label="Photo of RT hugging a client, laughing, with a pink tint"></div>
  <h2 class="headline center" style="top:230px;font-size:22px;line-height:23px;">Support When<br>Motivation Disappears</h2>
  <div class="divider" style="top:289px;"></div>
  <p class="tagline center" style="top:295px;">Stay Consistent with RT in Your Pocket!</p>
</section>

<section class="post" style="left:602px;top:48px;">
  <div class="photo photo-solo-pink" role="img" aria-label="Photo of RT smiling by a pool table, with a rose tint"></div>
  <h2 class="headline" style="left:14px;top:84px;font-size:25px;line-height:26.5px;">Eat the food<br>you love. Stay<br>accountable<br>every day.</h2>
  <p class="tagline" style="left:12px;top:272px;font-size:12px;line-height:21px;">Stay Consistent<br>with RT in Your Pocket!</p>
</section>

<section class="post" style="left:879px;top:48px;">
  <div class="photo photo-hug" role="img" aria-label="Photo of RT hugging a client, laughing, with a pink tint"></div>
  <h2 class="headline center" style="top:228px;font-size:20px;line-height:22px;">What if<br>RT Checked in Every Day?</h2>
  <div class="divider" style="top:285px;"></div>
  <p class="tagline center" style="top:294px;">Stay Consistent with RT in Your Pocket!</p>
</section>

<section class="post" style="left:29px;top:400px;background:var(--night);">
  <div style="position:absolute;left:7px;top:0;width:241px;height:116px;background:var(--rose);"></div>
  <div class="photo photo-pair" style="left:22px;top:82px;width:215px;height:215px;inset:auto;" role="img" aria-label="Photo of RT and a client standing together, laughing"></div>
  <h2 class="headline center" style="top:12px;font-size:25px;line-height:27px;">Stop Starting Over<br>Every Monday</h2>
  <p class="tagline center" style="top:302px;font-size:9.5px;">Stay Consistent with RT in Your Pocket!</p>
</section>

<section class="post" style="left:313px;top:400px;">
  <div class="photo photo-solo-dark" role="img" aria-label="Photo of RT smiling by a pool table"></div>
  <h2 class="headline" style="left:13px;top:121px;font-size:25px;line-height:27px;">The Missing<br>Piece Isn’t<br>Another Diet</h2>
  <p class="tagline" style="left:10px;top:296px;">Stay Consistent with RT in Your Pocket!</p>
</section>

<section class="post" style="left:605px;top:400px;background:var(--plum);">
  <svg style="position:absolute;left:0;top:0;" width="256" height="319" aria-hidden="true">
    <polygon points="0,164 256,125 256,286 0,286" fill="#c9587a"/>
    <rect x="0" y="286" width="256" height="33" fill="#5b2352"/>
  </svg>
  <div class="photo photo-pair" style="left:22px;top:48px;width:215px;height:238px;inset:auto;" role="img" aria-label="Photo of RT and a client standing together, laughing"></div>
  <h2 class="headline" style="left:8px;top:5px;font-size:22px;">When Motivation Fades,</h2>
  <h2 class="headline" style="right:12px;top:34px;font-size:18px;">RT Checks In</h2>
  <p class="tagline center" style="top:296px;">Stay Consistent with RT in Your Pocket!</p>
</section>

<section class="post" style="left:29px;top:749px;">
  <div class="photo photo-solo-night" role="img" aria-label="Photo of RT smiling by a pool table, fading into deep purple"></div>
  <h2 class="headline" style="left:9px;top:166px;font-size:25px;line-height:31px;">You don’t need more<br>willpower.</h2>
  <h2 class="headline" style="left:9px;top:240px;font-size:22px;color:var(--rose);">You need more support</h2>
  <p class="tagline" style="left:9px;top:284px;font-size:12px;color:var(--rose);">Stay Consistent with RT in Your Pocket!</p>
</section>

<section class="post" style="left:313px;top:749px;">
  <div class="photo photo-hug" role="img" aria-label="Photo of RT hugging a client, laughing, with a pink tint"></div>
  <h2 class="headline center" style="top:228px;font-size:20px;line-height:22px;">The Support System You’ve<br>Been Missing</h2>
  <div class="divider" style="top:286px;"></div>
  <p class="tagline center" style="top:295px;">Stay Consistent with RT in Your Pocket!</p>
</section>

<section class="post" style="left:604px;top:744px;">
  <div class="photo photo-solo-rose" role="img" aria-label="Photo of RT smiling, hand on hip, over a pink backdrop"></div>
  <svg style="position:absolute;left:0;top:0;" width="256" height="319" aria-hidden="true">
    <path d="M0,272 C60,250 170,262 256,278 L256,319 L0,319 Z" fill="#c9587a"/>
    <path d="M0,280 C60,258 170,264 256,278" fill="none" stroke="#f6dbe5" stroke-width="3"/>
  </svg>
  <h2 class="headline" style="left:12px;top:133px;font-size:17px;line-height:22.5px;">One Bad<br>Meal<br>Doesn’t Mean<br>You Failed</h2>
  <p class="tagline" style="left:12px;top:298px;font-size:12px;">Stay Consistent with RT in Your Pocket!</p>
</section>

</body>
</html>
```